Meridale Bed Company Needs Business Card

Looking for a very nice looking business card. Creative but not extravagant. We sell beds and pillows across the U.S. and need something professional but catchy. I have attached the logo.

Name : Devin Holt
Title : President
Phone : (800) 471-2960
Email: sleep@quilmora.com
Website: www.quilmora.com

Can be single-sided or double-sided
horizontal or vertical

Can use Blues/Greys

Target Market(s)

Mass Market

Industry/Entity Type

Retail

Contact Information for Business Card

Name : Devin Holt
Title : President
Phone : (800) 471-2960
Email: sleep@quilmora.com
Website: www.quilmora.com

Requirements
Must have
• Clean, Modern, Smooth
• Can use Blues/Greys
• On the other side without the information - have something simple like www.quilmora.com or our logo
Nice to have
• Surprise me
Should not have
• Nothing crazy, nothing cluttered

```html
<!DOCTYPE html>
<html lang="en">
<head>
<meta charset="utf-8">
<title>Meridale Bed Company – Stationery</title>
<link rel="stylesheet" href="https://fonts.googleapis.com/css2?family=Open+Sans:wght@400;600&display=swap">
<style>
  :root {
    --brand-blue: #2a9fdc;
    --brand-blue-deep: #1f8fcf;
    --ink: #3a3a3a;
    --ink-soft: #6b6b6b;
    --rule-grey: #9a9a9a;
    --paper: #ffffff;
    --backdrop: #efefef;
  }
  * { box-sizing: border-box; margin: 0; padding: 0; }
  html, body { width: 1200px; height: 789px; overflow: hidden; }
  body {
    background: var(--backdrop);
    font-family: "Open Sans", sans-serif;
    color: var(--ink);
    position: relative;
  }
  .wordmark {
    font-family: "Open Sans", sans-serif;
    font-weight: 400;
    color: var(--brand-blue);
    line-height: 1;
    white-space: nowrap;
  }

  /* Letterhead */
  .letterhead {
    position: absolute; left: 90px; top: 60px;
    width: 470px; height: 665px;
    background: var(--paper);
    box-shadow: 0 2px 10px rgba(0,0,0,0.08);
    padding: 52px 48px 0 48px;
  }
  .letterhead .wordmark { font-size: 36px; margin-bottom: 54px; }
  .letter { font-size: 8px; line-height: 1.55; color: var(--ink); }
  .letter p { margin-bottom: 10px; }
  .letter .address { margin-bottom: 12px; }
  .signature {
    width: 90px; height: 26px; margin: 6px 0 2px;
    background: linear-gradient(90deg, #d9d9d9, #eeeeee);
    border-radius: 3px;
  }
  .signer-title { font-weight: 600; }
  .letter-footer {
    position: absolute; left: 0; right: 0; bottom: 70px;
  }
  .footer-rule { display: flex; height: 3px; }
  .footer-rule .blue { flex: 1; background: var(--brand-blue); }
  .footer-rule .grey { width: 64px; background: var(--rule-grey); }
  .footer-web {
    text-align: right; padding: 8px 48px 0 0;
    font-size: 7px; color: var(--brand-blue);
  }
  .letter-edge {
    position: absolute; left: 0; bottom: 0; width: 62%; height: 4px;
    background: var(--brand-blue);
  }

  /* Business cards */
  .card {
    position: absolute; left: 660px; width: 440px; height: 252px;
    box-shadow: 0 2px 10px rgba(0,0,0,0.1);
  }
  .card-front { top: 95px; background: var(--paper); padding: 34px 36px; }
  .card-front .wordmark { font-size: 34px; }
  .card-tag {
    position: absolute; top: 36px; right: 0; width: 34px; height: 12px;
    background: var(--brand-blue-deep);
  }
  .person { margin-top: 44px; }
  .person-name { font-size: 11px; font-weight: 600; letter-spacing: 0.06em; color: var(--ink); }
  .person-title { font-size: 8px; letter-spacing: 0.1em; color: var(--ink-soft); margin-bottom: 12px; }
  .contact-list { list-style: none; font-size: 8.5px; color: var(--ink-soft); }
  .contact-list li { display: flex; align-items: center; gap: 8px; margin-bottom: 5px; }
  .contact-list svg { width: 9px; height: 9px; flex: none; }
  .card-rule {
    position: absolute; left: 0; right: 0; bottom: 0; height: 5px; display: flex;
  }
  .card-rule .blue { flex: 1; background: var(--brand-blue); }
  .card-rule .grey { width: 70px; background: var(--rule-grey); }

  .card-back {
    top: 420px; background: var(--brand-blue);
    display: flex; align-items: center; justify-content: center;
  }
  .card-back .wordmark { color: var(--paper); font-size: 64px; }
</style>
</head>
<body>

  <section class="letterhead">
    <div class="wordmark">quilmora</div>
    <div class="letter">
      <div class="address">
        November 1, 2015<br>
        Ms. Clara Pine<br>
        48 Orchard Row<br>
        Dayton, OH 45402
      </div>
      <p>Dear Ms. Pine,</p>
      <p>The first paragraph of a business letter states the main point of the letter. Begin with a friendly opening, then move quickly to the purpose of the letter. Use a couple of sentences to explain the purpose, but do not go into detail yet.</p>
      <p>Beginning with the second paragraph, state the supporting details to justify your purpose. These may take the form of background information, statistics or first-hand accounts. A few short paragraphs within the body of the letter should be enough to support your reasoning.</p>
      <p>Finally, in the closing paragraph, briefly restate your purpose and why it is important. If the purpose of your letter is related to your employment, consider ending with your contact information. Close with gratitude for the reader's time.</p>
      <p>Sincerely,</p>
      <div class="signature" role="img" aria-label="Handwritten signature"></div>
      <div class="signer-title">President</div>
    </div>
    <div class="letter-footer">
      <div class="footer-rule"><span class="blue"></span><span class="grey"></span></div>
      <div class="footer-web">www.quilmora.com</div>
    </div>
    <div class="letter-edge"></div>
  </section>

  <section class="card card-front">
    <div class="wordmark">quilmora</div>
    <div class="card-tag"></div>
    <div class="person">
      <div class="person-name">DEVIN HOLT</div>
      <div class="person-title">PRESIDENT</div>
      <ul class="contact-list">
        <li>
          <svg viewBox="0 0 10 10"><path d="M2 1h2l1 2.5-1.2 1a5 5 0 0 0 2.7 2.7l1-1.2L10 7v2a1 1 0 0 1-1 1A9 9 0 0 1 0 2a1 1 0 0 1 1-1z" fill="#2a9fdc"/></svg>
          (800) 471-2960
        </li>
        <li>
          <svg viewBox="0 0 10 10"><rect x="0.5" y="2" width="9" height="6" fill="none" stroke="#2a9fdc"/><path d="M0.5 2 5 5.5 9.5 2" fill="none" stroke="#2a9fdc"/></svg>
          sleep@quilmora.com
        </li>
        <li>
          <svg viewBox="0 0 10 10"><circle cx="5" cy="5" r="4.3" fill="none" stroke="#2a9fdc"/><path d="M0.7 5h8.6M5 0.7c-2.4 2.6-2.4 6 0 8.6M5 0.7c2.4 2.6 2.4 6 0 8.6" fill="none" stroke="#2a9fdc" stroke-width="0.8"/></svg>
          www.quilmora.com
        </li>
      </ul>
    </div>
    <div class="card-rule"><span class="blue"></span><span class="grey"></span></div>
  </section>

  <section class="card card-back">
    <div class="wordmark">quilmora</div>
  </section>

</body>
</html>
```